TK Homes - Stone Dorf Design

Looking for a double sides design, 1 side for my realestate and the other for home building. ( TK Homes on 1 side, Stone Dorf card on the other Side
Side 1 - Marek Tove ~ Vox Realty logo and Company ( the Property quarter )
Marek Tove
Marek@Marektove.example
IG - Marek_Bzq_Realtor
FB - marekt
Cell - 5558130467
3847 61 St Nw

Side 2
Marek Tove
5558130467
IG - Stonedorf_Bzq
Stonedorfdev@mailbox.example

Target Market(s)

Home buyers/ sellers

Industry/Entity Type

Home builders - Realestate

Contact Information for Business Card

Above

Requirements
Must have
• Black OR White background - my information -

```html
<!DOCTYPE html>
<html lang="en">
<head>
<meta charset="utf-8">
<title>Marek Tove – Business Cards</title>
<link rel="stylesheet" href="https://fonts.googleapis.com/css2?family=Cinzel:wght@400;600&family=Tinos&display=swap">
<style>
  :root {
    --page: #2a2a2c;
    --card: #1c1c1e;
    --accent: #1e7bd4;
    --ink: #ffffff;
    --ghost: #2b2b2e;
    --muted: #c9c9cc;
  }
  * { box-sizing: border-box; margin: 0; padding: 0; }
  html, body { width: 1200px; height: 900px; overflow: hidden; background: var(--page); }
  .sheet { position: relative; width: 1200px; height: 900px; }
  .card {
    position: absolute; left: 250px; width: 700px; height: 400px;
    background: var(--card); border-bottom: 6px solid var(--accent);
    overflow: hidden; font-family: "Tinos", serif; color: var(--ink);
  }
  .card--builder { top: 40px; }
  .card--realty { top: 460px; }

  .card__title {
    position: absolute; right: 48px; top: 40px;
    font-family: "Cinzel", serif; font-size: 30px; letter-spacing: 1px; text-align: right;
  }
  .card__title::after {
    content: ""; display: block; width: 60px; height: 2px; background: var(--accent);
    margin: 6px 0 0 auto;
  }

  .wordmark {
    position: absolute; left: 48px; top: 70px;
    font-family: "Cinzel", serif; font-weight: 600; font-size: 40px; letter-spacing: 2px;
    display: flex; align-items: center; gap: 12px;
  }
  .wordmark__square { width: 14px; height: 14px; background: var(--ink); }

  .ghost-name {
    position: absolute; right: 40px; top: 150px;
    font-family: "Cinzel", serif; font-weight: 600; font-size: 110px; line-height: 1;
    color: var(--ghost); text-align: right;
  }

  .contacts { position: absolute; left: 60px; bottom: 40px; list-style: none; font-size: 20px; }
  .contacts li { display: flex; align-items: center; gap: 12px; line-height: 30px; }
  .contacts svg { width: 16px; height: 16px; flex: none; fill: var(--accent); }

  .realtor-name {
    position: absolute; left: 48px; top: 60px;
    font-family: "Cinzel", serif; font-size: 50px; line-height: 1;
  }
  .realtor-name__first { color: var(--accent); }
  .realtor-name__last { color: var(--ink); }
  .realtor-name__mark { width: 16px; height: 16px; border: 2px solid var(--accent); display: inline-block; margin-right: 12px; }

  .card--realty .ghost-name { top: 110px; }
  .card--realty .contacts { bottom: 24px; font-size: 19px; }
  .card--realty .contacts li { line-height: 28px; }

  .affiliates {
    position: absolute; right: 48px; bottom: 40px;
    display: flex; gap: 24px; align-items: center;
    font-family: "Tinos", serif; font-size: 17px; color: var(--ink);
  }
</style>
</head>
<body>
<main class="sheet">

  <section class="card card--builder">
    <div class="wordmark"><span class="wordmark__square"></span>Stone Dorf</div>
    <h1 class="card__title">Marek Tove</h1>
    <div class="ghost-name" aria-hidden="true">Stone<br>Dorf</div>
    <ul class="contacts">
      <li><svg viewBox="0 0 16 16"><path d="M3 1l3 3-2 2c1 2 3 4 5 5l2-2 3 3-2 3C6 15 1 10 1 3z"/></svg>5558130467</li>
      <li><svg viewBox="0 0 16 16"><path d="M1 3h14v10H1zM2 4l6 5 6-5"/></svg>Stonedorfdev@mailbox.example</li>
      <li><svg viewBox="0 0 16 16"><circle cx="8" cy="8" r="7"/></svg>www.stonedorfdev.example</li>
      <li><svg viewBox="0 0 16 16"><rect x="1" y="1" width="14" height="14" rx="3"/></svg>Stonedorf_Bzq</li>
    </ul>
  </section>

  <section class="card card--realty">
    <h1 class="card__title">Marek Tove</h1>
    <div class="realtor-name">
      <span class="realtor-name__mark"></span><span class="realtor-name__first">Marek</span>
      <span class="realtor-name__last">Tove</span>
    </div>
    <div class="ghost-name" aria-hidden="true">Marek<br>Tove</div>
    <ul class="contacts">
      <li><svg viewBox="0 0 16 16"><path d="M3 1l3 3-2 2c1 2 3 4 5 5l2-2 3 3-2 3C6 15 1 10 1 3z"/></svg>5558130467</li>
      <li><svg viewBox="0 0 16 16"><path d="M1 3h14v10H1zM2 4l6 5 6-5"/></svg>Marek@Marektove.example</li>
      <li><svg viewBox="0 0 16 16"><circle cx="8" cy="8" r="7"/></svg>www.Marektove.example</li>
      <li><svg viewBox="0 0 16 16"><path d="M8 1a5 5 0 0 1 5 5c0 4-5 9-5 9S3 10 3 6a5 5 0 0 1 5-5z"/></svg>3847 61 St Nw</li>
      <li><svg viewBox="0 0 16 16"><rect x="1" y="1" width="14" height="14" rx="3"/></svg>Marek_Bzq_Realtor</li>
      <li><svg viewBox="0 0 16 16"><rect x="1" y="1" width="14" height="14"/></svg>marekt</li>
    </ul>
    <div class="affiliates">
      <span>the Property quarter</span>
      <span>Vox Realty</span>
    </div>
  </section>

</main>
</body>
</html>
```